- Redesign our business card
- Logo remains unchanged
- Current business card attached

Target Market(s)

We are a property management company

Industry/Entity Type

Business

```html
<!DOCTYPE html>
<html lang="en">
<head>
<meta charset="utf-8">
<title>Harcourt Property – Business Card</title>
<link rel="stylesheet" href="https://fonts.googleapis.com/css2?family=Archivo:wght@800&family=Big+Shoulders+Display:wght@400&display=swap">
<style>
  :root {
    --page: #ffffff;
    --card-start: #6b6d72;
    --card-end: #858146;
    --ink: #e4d4a9;
  }
  html, body {
    margin: 0;
    padding: 0;
    width: 1200px;
    height: 900px;
    overflow: hidden;
    background: var(--page);
  }
  .card {
    position: absolute;
    left: 0;
    top: 80px;
    width: 1200px;
    height: 740px;
    overflow: hidden;
    background: linear-gradient(120deg, var(--card-start) 0%, var(--card-end) 100%);
    color: var(--ink);
    font-family: "Big Shoulders Display", "Arial Narrow", sans-serif;
  }
  .holder-name {
    position: absolute;
    left: 76px;
    top: 58px;
    margin: 0;
    font-family: "Archivo", "Arial Black", sans-serif;
    font-weight: 800;
    font-size: 52px;
    letter-spacing: -1.5px;
    line-height: 1;
  }
  .holder-title {
    position: absolute;
    left: 76px;
    top: 128px;
    margin: 0;
    font-size: 54px;
    line-height: 1;
    letter-spacing: -0.5px;
    transform-origin: 0 50%;
    transform: scaleX(0.88);
    white-space: nowrap;
  }
  .contact {
    position: absolute;
    left: 0;
    width: 1100px;
    text-align: center;
    font-size: 54px;
    line-height: 1;
    margin: 0;
    white-space: nowrap;
    letter-spacing: -0.5px;
    transform-origin: 550px 50%;
  }
  .contact.postal { top: 260px; transform: scaleX(1.04); }
  .contact.street { top: 327px; transform: scaleX(0.92); }
  .contact.phones { top: 394px; transform: scaleX(0.84); }
  .contact.online {
    top: 460px;
    display: flex;
    justify-content: center;
    gap: 62px;
    transform: scaleX(0.84);
  }
  .services {
    position: absolute;
    left: 1086px;
    top: 684px;
    transform-origin: 0 0;
    transform: rotate(-90deg) scaleX(0.76);
    margin: 0;
    font-size: 40px;
    line-height: 1;
    white-space: nowrap;
  }
  .services span + span { margin-left: 22px; }
</style>
</head>
<body>
  <section class="card">
    <h1 class="holder-name">Daniel Harcourt</h1>
    <p class="holder-title">Licensed Strata Manager</p>

    <p class="contact postal">PO BOX 48, Northgate NSW 2019</p>
    <p class="contact street">12/6-20 Marlow Street Eastfield NSW 2016</p>
    <p class="contact phones">T: 02 9381 4725&nbsp; F: 02 93814726&nbsp; M: 0412 538 906</p>
    <p class="contact online">
      <span class="email">E: info@harcourtproperty.com.au</span>
      <span class="web">www.harcourtproperty.com.au</span>
    </p>

    <p class="services">
      <span>Strata Management</span><span>Community Management</span><span>Property Management</span>
    </p>
  </section>
</body>
</html>
```